Membership Based Medical Practice Website

We need a functioning website for a new Membership based medical practice. There will be an enrollment fee and a monthly fee. We would like to see designs that are modern, simple. Should use neutral light colors. Examples of sites we like are www.kellanmoorclinic.com and https://fernholtcare.com/ We also have a link that when "Join Now" is clicked it will go to the signup website.

Target Market(s)

Gay Men, local population, Age group 20 to 60's.

Industry/Entity Type

Medical

Coding

Coded - Design and coding required

Number of Pages Required

5+ page

Font styles to use
Sans Serif

Colors
ffffff
cee9f5
ecf7fb
cfeae6
edf8f6
aaaaaa
e9e9e9
dbdbdb
fff3d1

Requirements
Must have
• Logo and header on every page. Clean, simple design, clear content, mobile compatible.
• Must use Wordpress
Nice to have
• Ideas should come from kellanmoorclinic.com
• Easy to read
Should not have
• Generic patient pictures, bold colors.
• Should not copy from above websites.

```html
<!DOCTYPE html>
<html lang="en">
<head>
<meta charset="utf-8">
<title>Larkfield Infectious Disease Specialists</title>
<link rel="stylesheet" href="https://fonts.googleapis.com/css2?family=Montserrat:wght@300;400;500;600&display=swap">
<style>
:root{
  --white:#ffffff;
  --sky:#cee9f5;
  --sky-deep:#b9dfee;
  --sky-pale:#ecf7fb;
  --mint:#cfeae6;
  --mint-deep:#b5e0d9;
  --mint-pale:#edf8f6;
  --grey:#aaaaaa;
  --grey-light:#e9e9e9;
  --grey-mid:#dbdbdb;
  --cream:#fff3d1;
  --gold:#d4b063;
  --ink:#222222;
  --text:#555555;
  --section-grey:#f4f4f4;
}
*{margin:0;padding:0;box-sizing:border-box}
html,body{width:1200px;height:3789px;overflow:hidden;background:var(--white)}
body{font-family:'Montserrat',sans-serif;color:var(--ink);position:relative}
.abs{position:absolute}

/* header */
.top-rule{left:0;top:0;width:1200px;height:5px;background:var(--sky)}
.site-header{left:0;top:5px;width:1200px;height:101px;background:var(--white);z-index:3}
.brand-disc{left:87px;top:-110px;width:280px;height:287px;border-radius:50%;background:var(--white);z-index:4}
.brand{left:100px;top:50px;width:254px;text-align:center;z-index:5}
.brand-dot{width:46px;height:46px;border-radius:50%;border:2px solid var(--gold);margin:0 auto 10px}
.brand-name{font-size:14px;letter-spacing:9px;color:var(--ink);font-weight:400}
.brand-sub{font-size:10px;letter-spacing:.5px;color:var(--ink);margin-top:4px}
.main-nav{top:42px;left:498px;display:flex;gap:0;z-index:5;font-size:13px;font-weight:500}
.main-nav a{position:absolute;white-space:nowrap;color:var(--ink);text-decoration:none}
.join-btn{left:980px;top:32px;width:106px;height:38px;border-radius:19px;background:var(--mint-deep);color:var(--white);font-size:12px;font-weight:600;display:flex;align-items:center;justify-content:center;letter-spacing:1px;z-index:5;box-shadow:0 0 0 3px var(--mint-pale)}

/* hero */
.hero{left:0;top:106px;width:1200px;height:581px;background:linear-gradient(180deg,#8d8a86 0%,#b69a7c 45%,#d99a55 62%,#6f4a2b 85%,#3d2c20 100%)}
.hero-caption{left:230px;top:323px;width:738px;height:144px;background:rgba(190,225,240,.85);color:var(--white);font-size:30px;line-height:48px;text-align:center;display:flex;align-items:center;justify-content:center;font-weight:400;letter-spacing:1px}
.hero-dots{left:553px;top:613px;display:flex;gap:6px}
.hero-dots span{width:11px;height:11px;border-radius:50%;background:var(--white);opacity:.9}
.hero-dots span:first-child{background:transparent;border:2px solid var(--white)}

/* specialties */
.spec-heading{left:0;top:818px;width:1200px;text-align:center;font-size:21px;letter-spacing:.5px;color:var(--ink)}
.spec-tag{left:354px;top:861px;width:492px;height:41px;background:var(--sky);color:var(--white);font-size:17px;letter-spacing:.5px;display:flex;align-items:center;justify-content:center}
.spec-card{width:270px;height:205px;background:var(--white);border-radius:40px 8px 40px 8px;box-shadow:3px 6px 14px rgba(0,0,0,.12);display:flex;flex-direction:column;align-items:center;justify-content:flex-end;padding-bottom:26px}
.spec-card svg{position:absolute;top:30px;left:95px}
.spec-card p{font-size:11px;font-weight:600;text-align:center;line-height:22px;letter-spacing:.3px}
.view-more{left:493px;top:1490px;width:214px;height:58px;border-radius:29px;background:var(--mint-deep);color:var(--white);font-size:14px;letter-spacing:1px;display:flex;align-items:center;justify-content:center}

/* benefits */
.benefits{left:0;top:1680px;width:1200px;height:917px;background:var(--section-grey)}
.ben-title{left:349px;top:1798px;width:502px;height:51px;background:var(--sky);color:var(--white);font-size:29px;display:flex;align-items:center;justify-content:center;letter-spacing:1px;font-weight:300}
.ben-sub{left:0;top:1870px;width:1200px;text-align:center;font-size:19px}
.center-mark{left:480px;top:2140px;width:240px;height:240px;display:flex;align-items:center;justify-content:center;gap:10px}
.center-mark .ring{width:26px;height:26px;border-radius:50%;border:3px solid var(--gold)}
.center-mark span{font-size:22px;letter-spacing:6px;color:var(--gold)}
.feature{width:300px}
.feature h3{font-size:15px;font-weight:600;margin-bottom:10px}
.feature p{font-size:12px;line-height:21px;color:var(--text)}
.feature.left{text-align:right}
.icon-dot{width:66px;height:66px;border-radius:50%;display:flex;align-items:center;justify-content:center;transform:translate(-50%,-50%)}
.icon-dot.mint{background:var(--mint-deep)}
.icon-dot.sky{background:var(--sky-deep)}
.icon-dot.grey{background:#8b8b8b}
.icon-dot.cream{background:var(--cream);box-shadow:0 0 0 4px #fdf0c6 inset}

/* pricing */
.pricing{left:0;top:2597px;width:1200px;height:189px;background:var(--mint-deep);text-align:center;color:var(--white)}
.pricing h2{font-size:24px;font-weight:500;margin-top:50px;letter-spacing:.5px}
.pricing p{font-size:31px;font-weight:300;margin-top:14px;letter-spacing:.5px}
.pointer{left:570px;top:2785px;width:0;height:0;border-left:30px solid transparent;border-right:30px solid transparent;border-top:30px solid var(--mint-deep);z-index:2}
.includes{left:0;top:2786px;width:1200px;height:591px;background:linear-gradient(180deg,#3d4146 0%,#5c6066 35%,#6c6e5c 60%,#3c4029 100%)}
.inc-item{width:230px;text-align:center;color:var(--white)}
.inc-item svg{display:block;margin:0 auto}
.inc-item p{font-size:16px;line-height:24px;margin-top:22px;font-weight:500}
.inc-item small{display:block;font-size:11px;line-height:14px}
.arrow{top:2940px}
.learn-more{left:442px;top:3223px;width:316px;height:59px;border-radius:30px;background:var(--sky);color:var(--white);font-size:15px;letter-spacing:1px;display:flex;align-items:center;justify-content:center}

/* footer */
.foot-title{font-size:19px;font-weight:600;letter-spacing:.5px}
.foot-rule{width:46px;height:2px;background:var(--mint-deep)}
.foot-text{font-size:14px}
.book-btn{left:119px;top:3577px;width:255px;height:53px;border-radius:27px;background:var(--sky);color:var(--white);font-size:14px;letter-spacing:1px;display:flex;align-items:center;justify-content:center}
.quick-link{font-size:13px}
.foot-brand{left:820px;top:3455px;width:260px;text-align:center}
.foot-brand .ring{width:60px;height:60px;border-radius:50%;border:2px solid var(--gold);margin:0 auto 18px}
.foot-brand .name{font-size:19px;letter-spacing:10px;font-weight:400}
.foot-brand .sub{font-size:13px;margin-top:4px}
.foot-line{left:110px;top:3718px;width:980px;height:1px;background:var(--grey-mid)}
.copyright{left:110px;top:3746px;font-size:11px;color:var(--ink)}
.socials{left:1010px;top:3745px;display:flex;gap:8px}
.socials span{width:13px;height:13px;border-radius:50%;background:#333}
</style>
</head>
<body>

<div class="abs top-rule"></div>
<header class="abs site-header"></header>
<div class="abs brand-disc"></div>
<div class="abs brand">
  <div class="brand-dot"></div>
  <div class="brand-name">LARKFIELD</div>
  <div class="brand-sub">INFECTIOUS DISEASE SPECIALISTS</div>
</div>
<nav class="abs main-nav" style="left:0;top:45px;width:1200px">
  <a style="left:498px">HOME</a>
  <a style="left:566px">SPECIALTIES</a>
  <a style="left:677px">PRICING</a>
  <a style="left:763px">ABOUT US</a>
  <a style="left:859px">FAQ</a>
  <a style="left:914px">BLOG</a>
</nav>
<div class="abs join-btn">JOIN US</div>

<section class="abs hero" role="img" aria-label="Photo of friends standing arm in arm on a hill at sunset"></section>
<div class="abs hero-caption">SPECIALTY MEDICINE WITH COMMITMENT,<br>COMPASSION AND CARE</div>
<div class="abs hero-dots"><span></span><span></span><span></span><span></span><span></span><span></span></div>

<h2 class="abs spec-heading">WE OFFER COMPREHENSIVE TREATMENT OF A WIDE VARIETY OF INFECTIOUS DISEASES.</h2>
<div class="abs spec-tag">OUT EXPERTISE IS IN THE FOLLOWING AREA</div>

<div class="abs spec-card" style="left:167px;top:975px">
  <svg width="80" height="90" viewBox="0 0 80 90" fill="none" stroke="#666" stroke-width="2"><path d="M40 10c-10 0-14 8-12 18l30 56h10L32 30c-1-8 3-12 8-12s9 4 8 12L14 84h10l30-56c2-10-4-18-14-18z"/></svg>
  <p>HIV/PREP</p>
</div>
<div class="abs spec-card" style="left:465px;top:975px">
  <svg width="80" height="90" viewBox="0 0 80 90" fill="none" stroke="#7cc3dc" stroke-width="2"><path d="M12 40c0-16 20-22 36-20s22 10 18 22-20 22-34 20S12 52 12 40z"/><path d="M40 20v26"/></svg>
  <p>CHRONIC HEPATITIS</p>
</div>
<div class="abs spec-card" style="left:763px;top:975px">
  <svg width="80" height="90" viewBox="0 0 80 90" fill="none" stroke="#666" stroke-width="2"><circle cx="22" cy="52" r="14"/><path d="M22 20v18M14 28h16"/><circle cx="58" cy="30" r="14"/><path d="M58 44v20M50 56l8 10 8-10"/></svg>
  <p>SEXUALLY TRANSMITTED<br>INFECTIONS</p>
</div>
<div class="abs spec-card" style="left:167px;top:1207px">
  <svg width="80" height="90" viewBox="0 0 80 90" fill="none" stroke="#666" stroke-width="2"><path d="M20 62l36-36 8 8-36 36z"/><path d="M56 26l10-10M62 12l8 8M20 62l-10 10M8 60l14 14"/><path d="M30 52l4 4M38 44l4 4M46 36l4 4"/></svg>
  <p>PRE-TRAVEL VACCINATIONS<br>AND COUNSELLING</p>
</div>
<div class="abs spec-card" style="left:465px;top:1207px">
  <svg width="80" height="90" viewBox="0 0 80 90" fill="none" stroke="#666" stroke-width="2"><rect x="28" y="8" width="24" height="40" rx="6"/><path d="M34 20h12M40 48v14M36 62h8v8h-8zM40 70v12"/></svg>
  <p>INFECTIONS ASSOCIATED<br>WITH MEDICAL DEVICES</p>
</div>
<div class="abs spec-card" style="left:763px;top:1207px">
  <svg width="80" height="90" viewBox="0 0 80 90" fill="none" stroke="#666" stroke-width="2"><path d="M30 10c-6 0-8 8-4 12l8 32c-4 4-2 12 4 12s8-4 8-8l-4-6 8-30c4-2 2-12-4-12-4 0-6 4-6 4s-4-4-10-4z"/><path d="M38 66v14M46 66v12"/></svg>
  <p>BONE AND JOINT<br>INFECTIONS</p>
</div>
<div class="abs view-more">VIEW MORE</div>

<section class="abs benefits"></section>
<div class="abs ben-title">LESS WAIT, MORE PERSONAL</div>
<div class="abs ben-sub">WE ARE NOT YOUR TRADITIONAL DOCTOR'S OFFICE</div>
<div class="abs center-mark"><div class="ring"></div><span>LARKFIELD</span></div>

<!-- left column -->
<div class="abs feature left" style="left:16px;top:2003px"><h3>Straightforward pricing</h3><p>We charge all our patients the<br>same low rate - no surprises.</p></div>
<div class="abs icon-dot mint" style="left:356px;top:2039px"><svg width="30" height="30" viewBox="0 0 30 30" fill="#fff"><path d="M3 4v10l13 13 11-11L14 3H4zM9 7a2 2 0 110 4 2 2 0 010-4z"/></svg></div>

<div class="abs feature left" style="left:20px;top:2137px"><h3>Available when you are</h3><p>New patient appointments<br>are available within 1 week.</p></div>
<div class="abs icon-dot sky" style="left:371px;top:2175px"><svg width="28" height="28" viewBox="0 0 28 28" fill="#fff"><path d="M3 12h5v13H3zM10 12l5-9c2 0 3 2 2 5l-1 3h7c2 0 3 2 2 4l-3 8c-1 2-2 2-4 2h-8z"/></svg></div>

<div class="abs feature left" style="left:38px;top:2276px"><h3>Hassle-free booking</h3><p>Schedule your appointment<br>online at your convenience.</p></div>
<div class="abs icon-dot grey" style="left:389px;top:2314px"><svg width="30" height="30" viewBox="0 0 30 30" fill="none" stroke="#fff" stroke-width="2.5"><rect x="4" y="5" width="22" height="15" rx="1"/><path d="M11 25h8M15 20v5"/></svg></div>

<div class="abs feature left" style="left:56px;top:2410px"><h3>Devoted care</h3><p>We schedule enough time at<br>each visit to make sure all of</p></div>
<div class="abs icon-dot cream" style="left:407px;top:2448px"><svg width="28" height="28" viewBox="0 0 28 28" fill="#fff"><path d="M14 24L4 14a5.5 5.5 0 0110-7 5.5 5.5 0 0110 7z"/></svg></div>

<!-- right column -->
<div class="abs feature" style="left:897px;top:2003px"><h3>Within your reach</h3><p>Follow-up appointments may<br>be done by video chat for</p></div>
<div class="abs icon-dot cream" style="left:841px;top:2039px"><svg width="30" height="30" viewBox="0 0 30 30" fill="none" stroke="#e8c97a" stroke-width="2"><circle cx="15" cy="15" r="11"/><circle cx="15" cy="15" r="6"/><circle cx="15" cy="15" r="2" fill="#e8c97a"/></svg></div>

<div class="abs feature" style="left:877px;top:2137px"><h3>Save on lab costs</h3><p>If paying upfront for labs, we<br>offer discounted pricing.</p></div>
<div class="abs icon-dot grey" style="left:826px;top:2175px"><svg width="28" height="28" viewBox="0 0 28 28" fill="#fff"><path d="M10 3h8v2h-1v7l7 11c1 2 0 3-2 3H6c-2 0-3-1-2-3l7-11V5h-1z"/></svg></div>

<div class="abs feature" style="left:859px;top:2276px"><h3>Save on medications</h3><p>We offer deeply discounted<br>wholesale price medications for.</p></div>
<div class="abs icon-dot sky" style="left:808px;top:2314px"><svg width="28" height="28" viewBox="0 0 28 28" fill="#fff"><path d="M4 24C4 10 12 4 25 4c0 13-6 20-19 20zM6 22l12-12" stroke="#b9dfee" stroke-width="1.5"/></svg></div>

<div class="abs feature" style="left:844px;top:2410px"><h3>No middle man</h3><p>We don't bill any insurance<br>plans so decisions about your.</p></div>
<div class="abs icon-dot mint" style="left:793px;top:2448px"><svg width="28" height="28" viewBox="0 0 28 28" fill="#fff"><circle cx="14" cy="7" r="4.5"/><path d="M8 13h12v8h-2v6h-8v-6H8z"/></svg></div>

<section class="abs pricing">
  <h2>OUR PRICING IS SIMPLE, TRANSPARENT AND AFFORDABLE.</h2>
  <p>Membership Plan $80/mo, plus a one-time $99 enrollment fee.</p>
</section>
<div class="abs pointer"></div>

<section class="abs includes" role="img" aria-label="Photo of an empty road running through green hills under a cloudy sky"></section>

<div class="abs inc-item" style="left:120px;top:2883px">
  <svg width="160" height="160" viewBox="0 0 160 160"><rect x="33" y="33" width="94" height="94" transform="rotate(45 80 80)" fill="rgba(0,0,0,.35)" stroke="#fff" stroke-width="3"/><path d="M62 66h22M62 98h36V84M62 66v32M90 58l12 12-18 18H72V76z" fill="none" stroke="#fff" stroke-width="4"/></svg>
  <p>Includes all appointments,<br>No co-pay</p>
</div>
<div class="abs inc-item" style="left:373px;top:2883px">
  <svg width="160" height="160" viewBox="0 0 160 160"><rect x="33" y="33" width="94" height="94" transform="rotate(45 80 80)" fill="rgba(0,0,0,.35)" stroke="#fff" stroke-width="3"/><circle cx="80" cy="70" r="11" fill="#fff"/><path d="M60 100c0-12 8-18 20-18s20 6 20 18z" fill="#fff"/></svg>
  <p>Relaxed,<br>unrushed visits</p>
</div>
<div class="abs inc-item" style="left:625px;top:2883px">
  <svg width="160" height="160" viewBox="0 0 160 160"><rect x="33" y="33" width="94" height="94" transform="rotate(45 80 80)" fill="rgba(0,0,0,.35)" stroke="#fff" stroke-width="3"/><path d="M68 62l8 0 4 10-6 4c3 6 7 10 12 12l4-6 10 4v8c0 3-2 4-5 4-18-2-30-14-32-32 0-3 2-4 5-4z" fill="#fff"/></svg>
  <p>Direct communication with<br>your doctor via phone,<br>email, video chat 24/7</p>
</div>
<div class="abs inc-item" style="left:878px;top:2883px">
  <svg width="160" height="160" viewBox="0 0 160 160"><rect x="33" y="33" width="94" height="94" transform="rotate(45 80 80)" fill="rgba(0,0,0,.35)" stroke="#fff" stroke-width="3"/><rect x="60" y="64" width="40" height="34" rx="3" fill="none" stroke="#fff" stroke-width="4"/><path d="M60 74h40M68 58v10M92 58v10" stroke="#fff" stroke-width="4"/><rect x="68" y="80" width="8" height="7" fill="#fff"/></svg>
  <p>Convenient online<br>scheduling<small>(no need to call during<br>business hours)</small></p>
</div>
<svg class="abs arrow" style="left:74px" width="28" height="46" viewBox="0 0 28 46"><path d="M22 4L6 23l16 19" fill="none" stroke="#fff" stroke-width="5"/></svg>
<svg class="abs arrow" style="left:1100px" width="28" height="46" viewBox="0 0 28 46"><path d="M6 4l16 19L6 42" fill="none" stroke="#fff" stroke-width="5"/></svg>
<div class="abs learn-more">LEARN MORE ABOUT US</div>

<footer>
  <div class="abs foot-title" style="left:119px;top:3450px">OFFICE HOURS</div>
  <div class="abs foot-rule" style="left:119px;top:3486px"></div>
  <div class="abs foot-text" style="left:119px;top:3523px">Mon-Fri&nbsp;&nbsp;&nbsp;By appointment only</div>
  <div class="abs book-btn">BOOK APPOINTMENT</div>

  <div class="abs foot-title" style="left:495px;top:3450px">QUICK LINKS</div>
  <div class="abs foot-rule" style="left:495px;top:3486px"></div>
  <div class="abs quick-link" style="left:495px;top:3526px">HOME</div>
  <div class="abs quick-link" style="left:495px;top:3566px">SPECIALTIES</div>
  <div class="abs quick-link" style="left:495px;top:3604px">PRICING</div>
  <div class="abs quick-link" style="left:634px;top:3526px">ABOUT US</div>
  <div class="abs quick-link" style="left:634px;top:3566px">FAQ</div>
  <div class="abs quick-link" style="left:634px;top:3604px">BLOG</div>

  <div class="abs foot-brand">
    <div class="ring"></div>
    <div class="name">LARKFIELD</div>
    <div class="sub">INFECTIOUS DISEASE SPECIALISTS</div>
  </div>

  <div class="abs foot-line"></div>
  <div class="abs copyright">Copyrights @ 2019 Companyname.All Rights Reserved &nbsp;|&nbsp; Privacy Policy</div>
  <div class="abs socials"><span></span><span></span><span></span><span></span></div>
</footer>

</body>
</html>
```